Tour Guide in Israel business card

I am a tour guide in Israel (the holy land). Prior to it I have over 20 years high-tech business. My main (but not only) focus is working with business people that come to Israel and want to get a tour (usually short from few hours to 2 days). During my guiding I incorporate a lot of my know how of the Israeli business culture. I like to have a business card that I can present to anyone that is looking for a tour guide, but that business people will understand the additional value I can provide them during my tour.

Target Market(s)

Business visitors and tourist to Israel

Industry/Entity Type

Tourism

Contact Information for Business Card

Danny Korvath
email: danny@korvath-tours.example
Mobile: +972-52-7416205

Colors

Designer to choose colors to be used in the design.

Requirements
Must have
• Tour Guide
Nice to have
• I don't know how but it should project my understanding in business not just the tourist side of my knowledge.

```html
<!DOCTYPE html>
<html lang="en">
<head>
<meta charset="utf-8">
<title>Tour Guide – Business Card</title>
<link href="https://fonts.googleapis.com/css2?family=Exo+2:wght@500;600;700&family=Open+Sans:wght@400&display=swap" rel="stylesheet">
<style>
  :root {
    --stage: #1f2022;
    --card-blue: #2a7dbf;
    --brand-blue: #1f73bd;
    --paper: #ffffff;
    --ink-grey: #6b6f74;
    --white: #ffffff;
  }
  * { margin: 0; padding: 0; box-sizing: border-box; }
  html, body { width: 1200px; height: 900px; overflow: hidden; }
  body {
    background: var(--stage);
    position: relative;
    font-family: "Open Sans", sans-serif;
  }
  .card {
    position: absolute;
    left: 280px;
    width: 640px;
    height: 366px;
  }
  .card--front {
    top: 60px;
    background: var(--card-blue);
    display: flex;
    flex-direction: column;
    align-items: center;
    justify-content: center;
    gap: 24px;
  }
  .front-ring {
    width: 124px;
    height: 124px;
    border: 2px solid var(--white);
    border-radius: 50%;
  }
  .service-title {
    font-family: "Exo 2", sans-serif;
    font-weight: 700;
    font-size: 30px;
    letter-spacing: 6px;
    color: var(--white);
    text-transform: uppercase;
  }
  .card--back {
    top: 474px;
    background: var(--paper);
  }
  .identity {
    position: absolute;
    right: 390px;
    top: 150px;
    text-align: right;
  }
  .person-name {
    font-family: "Exo 2", sans-serif;
    font-weight: 600;
    font-size: 25px;
    color: var(--brand-blue);
    text-transform: uppercase;
    line-height: 1.1;
    white-space: nowrap;
  }
  .person-role {
    font-size: 13px;
    letter-spacing: 1.5px;
    color: var(--ink-grey);
    text-transform: uppercase;
    margin-top: 3px;
    white-space: nowrap;
  }
  .divider {
    position: absolute;
    left: 270px;
    top: 150px;
    width: 1.5px;
    height: 42px;
    background: var(--brand-blue);
  }
  .contact {
    position: absolute;
    left: 290px;
    top: 150px;
    list-style: none;
    font-size: 16px;
    color: var(--ink-grey);
    letter-spacing: 0.3px;
  }
  .contact li {
    display: flex;
    align-items: center;
    gap: 10px;
    height: 21px;
    white-space: nowrap;
  }
  .contact svg { width: 11px; height: 11px; flex: none; }
  .back-brand {
    position: absolute;
    right: 28px;
    bottom: 26px;
    display: flex;
    align-items: center;
    gap: 12px;
  }
  .back-brand-name {
    font-family: "Exo 2", sans-serif;
    font-weight: 700;
    color: var(--brand-blue);
    font-size: 15px;
    letter-spacing: 2px;
    text-transform: uppercase;
  }
  .back-ring {
    width: 84px;
    height: 84px;
    border: 2px solid var(--brand-blue);
    border-radius: 50%;
  }
</style>
</head>
<body>
  <section class="card card--front">
    <div class="front-ring"></div>
    <div class="service-title">Tour Guide</div>
  </section>

  <section class="card card--back">
    <div class="identity">
      <div class="person-name">Danny Korvath</div>
      <div class="person-role">Business Tour Guide</div>
    </div>
    <div class="divider"></div>
    <ul class="contact">
      <li>
        <svg viewBox="0 0 12 12" aria-hidden="true"><path d="M3 1 L5 3.5 L4 5 Q5 7.5 7 8 L8.5 7 L11 9 L9.5 11 Q3 10.5 1 2.5 Z" fill="#1f73bd"/></svg>
        <span>+972-52-7416205</span>
      </li>
      <li>
        <svg viewBox="0 0 12 12" aria-hidden="true"><rect x="1" y="2.5" width="10" height="7" fill="none" stroke="#1f73bd" stroke-width="1.3"/><path d="M1 2.5 L6 6.5 L11 2.5" fill="none" stroke="#1f73bd" stroke-width="1.3"/></svg>
        <span>danny@korvath-tours.example</span>
      </li>
    </ul>
    <div class="back-brand">
      <div class="back-brand-name">Korvath</div>
      <div class="back-ring"></div>
    </div>
  </section>
</body>
</html>
```